Residential Mortgage Leader needs Wordpress Design

Looking for a home page website design for a client. We develop using the WordPress platform and would prefer the design be at least loosely based on an existing WordPress template. Attached files have many notes from our creative brief with client. The site must be responsive. Approved, basic wireframe attached. There is room for interpretation.

Existing web site: http://www.marisolkettering.example/

The Marisol Kettering Team relies on strong systems to deliver an on-time, done-right, friendly experience. Marisol offers mortgages and refinancing services throughout the United States. She is a successful Brookvale Funding agent who strives to be an active part of her community. She would like to focus the site on her team, rather than just her.

Difference makers...
When you work with the Marisol Kettering team you get a high level of expertise and a friendly experience.

She has amazing credentials. Marisol is widely recognized as a top producer for her company, and has earned a number of awards and honors for her customer service.

Marisol's team is very engaged and enjoys sharing social comments or photos from their community.

Imagery:
* Friendly, warm imagery, preferably of her team or an image to represent her team
* Clean and crisp
* Professional / Experts in mortgage and refinance
* Clean / Good use of white space
Updates

When possible, please use imagery from the DFW area. The client mentioned they would prefer not to see stock images. Thanks.

Amend that- creative use of stock images, however, is fine. A few designs have used stock imagery, but in a well-considered manner.

We added some photos and graphics that are local. We are Dallas / Ft. Worth, Plano, Frisco, Texas. We also added some examples of photos to use for the "In the Community" area. Stock photos of business folks just doesn't fit there. Thanks!

Target Market(s)

They service a lot of builders, but also work with homeowners. Their typical client is usually a woman searching for mortgage services online. She typically has a family and may refer her husband to Marisol's team. Keep in mind, however, they also see a number of other scenarios. Most of their clients are middle to high-end borrowers.

Industry/Entity Type

It Company

Requirements
Must have
• Design should be developed using program such as Photoshop or Fireworks or Illustrator as last preference. Ideally, the design would be based on an existing responsive WordPress theme, which we would customize. You must include the name of the target theme. The footer should include lots of space for disclaimers and legal language. Site navigation should include these choices: "Home, About, Builders, Mortgage Info, Approval, Blog, Contact"
Nice to have
• Blog, social media and photos area. Use of the already approved style prototype with colors and fonts (Lato- a Google font, Times New Roman and Cookie-a decorative Google font). However, we are open to interpretation.
Should not have
• Hard to read fonts or a lack of white space.

```html
<!DOCTYPE html>
<html lang="en">
<head>
<meta charset="utf-8">
<title>Brookvale Funding – Marisol Kettering Team</title>
<link href="https://fonts.googleapis.com/css2?family=Lato:wght@400;700&family=Cookie&family=Tinos&display=swap" rel="stylesheet">
<style>
:root{
  --red:#c8231b;
  --ink:#3b3b3b;
  --hero:#575757;
  --hero-dark:#4d4d4d;
  --blue:#1689bd;
  --footer:#343434;
  --footer-bar:#2b2b2b;
  --muted:#d4d4d4;
  --body:#5a5a5a;
  --white:#fff;
}
*{box-sizing:border-box;margin:0;padding:0}
html,body{width:852px;height:1200px;overflow:hidden}
body{position:relative;font-family:"Lato",sans-serif;background:#fafafa;color:var(--body)}
.abs{position:absolute}
.serif{font-family:"Tinos","Times New Roman",serif}
.script{font-family:"Cookie",cursive}

.site-header{left:0;top:0;width:852px;height:92px;background:#f9f9f9}
.brand{left:78px;top:28px;display:flex;align-items:center;gap:8px}
.brand-mark{width:16px;height:16px;border-radius:50%;background:var(--red)}
.brand-name{font-size:22px;font-weight:700;color:var(--red);letter-spacing:-.3px}
.brand-sub{left:78px;top:54px;font-size:11px;font-weight:700;color:#444}
.work-with{left:640px;top:22px;display:flex;gap:6px;align-items:center}
.work-with .lbl{font-size:12px;color:#555;line-height:14px}
.work-with .num{font-size:13.5px;color:var(--red);line-height:16px}

.main-nav{left:0;top:92px;width:852px;height:38px;background:var(--ink)}
.main-nav ul{position:absolute;left:78px;top:0;display:flex;list-style:none;border-left:1px solid #2d2d2d}
.main-nav li{width:99.5px;height:38px;line-height:38px;text-align:center;color:#fff;font-size:11.5px;border-right:1px solid #2d2d2d}
.main-nav li.active{background:var(--red)}

.hero{left:0;top:130px;width:852px;height:302px;background:repeating-linear-gradient(45deg,var(--hero) 0 2px,var(--hero-dark) 2px 3px)}
.hero-photo{left:78px;top:27px;width:378px;height:249px;background:linear-gradient(135deg,#8fa6b3,#c9b9a6 45%,#5b7fae)}
.hero-title{left:473px;top:22px;font-size:38px;color:#fff;line-height:40px}
.hero-copy{left:473px;top:78px;width:300px;font-size:9.6px;line-height:12.8px;color:#f0f0f0}
.hero-copy p{margin-bottom:8px}
.btn-know{left:473px;top:243px;width:108px;height:32px;background:#fff;color:#222;font-size:14px;line-height:32px;text-align:center}
.hero-rule{left:0;top:432px;width:852px;height:3px;background:var(--red)}

.features{left:0;top:435px;width:852px;height:209px;background:#fbfbfb}
.feat-head{top:25px;height:35px;display:flex}
.feat-head .icon{width:47px;height:35px;background:var(--red);display:flex;align-items:center;justify-content:center}
.feat-head .title{flex:1;background:var(--ink);color:#fff;font-size:18px;line-height:35px;text-align:center;letter-spacing:.5px}
.cred-head{left:78px;top:25px;width:253px;height:35px;background:var(--red);color:#fff;font-size:21px;line-height:35px;padding-left:14px}
.feat-text{top:79px;font-size:9.6px;line-height:12.8px;color:var(--body)}
.feat-text p{margin-bottom:8px}

.community{left:0;top:644px;width:852px;height:298px;background:var(--blue);color:#fff}
.comm-title{left:0;top:4px;width:852px;text-align:center;font-size:38px}
.comm-sub{left:0;top:52px;width:852px;text-align:center;font-size:16px}
.comm-rule{left:0;width:852px;height:1px;background:#fff}
.col-head{top:113px;font-size:16px}
.blog-item{width:190px}
.blog-item h4{font-size:12.5px;font-weight:400;margin-bottom:2px}
.blog-item p{font-size:9.6px;line-height:12.8px;color:#e6f3fa}
.social-box{width:38px;height:36px;background:#fff}
.social-name{font-size:12.5px}
.social-desc{font-size:9.6px;color:#e6f3fa}
.tile{width:61px;height:57px;border:2px solid #fff}

.site-footer{left:0;top:942px;width:852px;height:210px;background:var(--footer);color:var(--muted)}
.agent-photo{left:78px;top:42px;width:103px;height:117px;border:1px solid #555;background:linear-gradient(160deg,#6b5a4d,#b99a80 60%,#3f3a3a)}
.agent-name{left:187px;top:46px;font-size:13px;line-height:16px;color:#fff}
.agent-info{left:188px;top:76px;font-size:9.6px;line-height:16.4px}
.directions{left:188px;top:191px;font-size:9.6px;color:#fff}
.foot-head{top:46px;font-size:13px;color:#fff}
.foot-list{top:76px;font-size:9.6px;line-height:16.4px;list-style:none}
.lang{left:613px;top:175px;width:77px;height:23px;background:#2a2a2a;font-size:9.6px;line-height:23px;padding-left:8px;color:#ddd}
.lang svg{position:absolute;right:8px;top:8px}

.foot-bar{left:0;top:1152px;width:852px;height:48px;background:var(--footer-bar)}
.copy{left:89px;top:17px;font-size:9.6px;color:#ccc}
.mini{top:13px;width:24px;height:24px}
</style>
</head>
<body>

<header class="abs site-header">
  <div class="abs brand"><span class="brand-mark"></span><span class="brand-name">Brookvale Funding</span></div>
  <div class="abs brand-sub">A Ridgewater Capital Company</div>
  <div class="abs work-with">
    <svg width="24" height="28" viewBox="0 0 24 28"><path d="M4 14a8 8 0 0 1 16 0" fill="none" stroke="#333" stroke-width="2"/><rect x="2" y="13" width="5" height="9" rx="2" fill="#333"/><rect x="17" y="13" width="5" height="9" rx="2" fill="#333"/><path d="M19 22q0 4-6 4" fill="none" stroke="#333" stroke-width="1.5"/></svg>
    <div><div class="lbl">Work With Us:</div><div class="num">0800-5550-123-4</div></div>
  </div>
</header>

<nav class="abs main-nav">
  <ul>
    <li class="active">Home</li><li>About Us</li><li>Builders</li><li>Mortgage Info</li><li>Approval</li><li>Blog</li><li>Contact Us</li>
  </ul>
</nav>

<section class="abs hero">
  <div class="abs hero-photo" role="img" aria-label="Smiling couple sitting outside their new home by a pool"></div>
  <h1 class="abs hero-title script" style="font-weight:400">Earning Your Business</h1>
  <div class="abs hero-copy">
    <p>Sed ut perspiciatis unde omnis iste natus error sit voluptatem accusantium doloremque laudantium, totam rem aperiam, eaque ipsa quae ab illo inventore veritatis et quasi architecto beatae vitae dicta sunt explicabo.</p>
    <p>Nemo enim ipsam voluptatem quia voluptas sit aspernatur aut odit aut fugit, sed quia consequuntur magni dolores eos qui ratione voluptatem sequi nesciunt.</p>
    <p>Neque porro quisquam est, qui dolorem ipsum quia dolor sit amet, consectetur, adipisci velit, sed quia non numquam eius modi tempora incidunt ut labore et dolore magnam aliquam quaerat voluptatem.</p>
  </div>
  <div class="abs btn-know serif">Get to Know Us</div>
</section>
<div class="abs hero-rule"></div>

<section class="abs features">
  <div class="abs cred-head serif">Our Credentials</div>
  <div class="abs feat-text" style="left:92px;width:240px">
    <p>Sed ut perspiciatis unde omnis iste natus error sit voluptatem accusantium doloremque laudantium, totam rem aperiam, eaque ipsa quae ab illo inventore veritatis et quasi architecto beatae vitae dicta sunt explicabo.</p>
    <p>Nemo enim ipsam voluptatem quia voluptas sit aspernatur aut odit aut fugit...</p>
  </div>

  <div class="abs feat-head" style="left:350px;width:203px">
    <div class="icon"><svg width="22" height="18" viewBox="0 0 22 18"><circle cx="11" cy="5" r="4" fill="#fff"/><circle cx="5" cy="12" r="4" fill="#fff"/><circle cx="17" cy="12" r="4" fill="#fff"/></svg></div>
    <div class="title serif">AWARDS</div>
  </div>
  <div class="abs feat-text" style="left:362px;width:188px">
    <p>Sed ut perspiciatis unde omnis iste natus error sit voluptatem accusantium doloremque laudantium, totam rem aperiam, eaque ipsa quae ab illo inventore veritatis et quasi architecto beatae vitae dicta sunt explicabo.</p>
  </div>

  <div class="abs feat-head" style="left:571px;width:203px">
    <div class="icon"><svg width="18" height="22" viewBox="0 0 18 22"><ellipse cx="9" cy="11" rx="7" ry="9" fill="none" stroke="#fff" stroke-width="1.5"/><ellipse cx="9" cy="11" rx="4" ry="6" fill="none" stroke="#fff" stroke-width="1.5"/><ellipse cx="9" cy="11" rx="1.5" ry="3" fill="#fff"/></svg></div>
    <div class="title serif">AWARDS</div>
  </div>
  <div class="abs feat-text" style="left:579px;width:190px">
    <p>Sed ut perspiciatis unde omnis iste natus error sit voluptatem accusantium doloremque laudantium, totam rem aperiam, eaque ipsa quae ab illo inventore veritatis et quasi architecto beatae vitae dicta sunt explicabo.</p>
  </div>
</section>

<section class="abs community">
  <h2 class="abs comm-title script" style="font-weight:400">Engaged In Our Community</h2>
  <div class="abs comm-sub serif">Connect With Us</div>
  <div class="abs comm-rule" style="top:81px"></div>
  <div class="abs comm-rule" style="top:85px"></div>

  <h3 class="abs col-head serif" style="left:78px;font-weight:400">Blog</h3>
  <div class="abs blog-item" style="left:78px;top:143px">
    <h4>• Borrowing</h4>
    <p>Sed ut perspiciatis unde omnis iste natus error sit voluptatem accusantium doloremque laudantium...</p>
  </div>
  <div class="abs blog-item" style="left:78px;top:209px">
    <h4>• Best Practices</h4>
    <p>Sed ut perspiciatis unde omnis iste natus error sit voluptatem accusantium doloremque laudantium...</p>
  </div>

  <h3 class="abs col-head serif" style="left:334px;font-weight:400">Social Icons</h3>
  <div class="abs social-box" style="left:334px;top:145px"></div>
  <div class="abs social-name" style="left:384px;top:146px">Friendhub</div>
  <div class="abs social-desc" style="left:384px;top:166px">Lorem ipsum dolor sit amet...</div>
  <div class="abs social-box" style="left:334px;top:187px"></div>
  <div class="abs social-name" style="left:384px;top:188px">Chirpline</div>
  <div class="abs social-desc" style="left:384px;top:208px">Lorem ipsum dolor sit amet...</div>
  <div class="abs social-box" style="left:334px;top:230px"></div>
  <div class="abs social-name" style="left:384px;top:231px">Rss</div>
  <div class="abs social-desc" style="left:384px;top:251px">Lorem ipsum dolor sit amet...</div>

  <h3 class="abs col-head serif" style="left:577px;font-weight:400">In The Community</h3>
  <div class="abs tile" style="left:577px;top:145px;background:linear-gradient(135deg,#d9823d,#4f8fc6)" role="img" aria-label="Group of children in bright shirts"></div>
  <div class="abs tile" style="left:645px;top:145px;background:linear-gradient(135deg,#5d6b7a,#d8d0c6)" role="img" aria-label="Team of young adults standing together"></div>
  <div class="abs tile" style="left:713px;top:145px;background:linear-gradient(135deg,#a86b5a,#c9c3bc)" role="img" aria-label="Volunteers outside a building"></div>
  <div class="abs tile" style="left:577px;top:209px;background:linear-gradient(135deg,#c8b8a6,#6e8aa6)" role="img" aria-label="Friends in a circle seen from above"></div>
  <div class="abs tile" style="left:645px;top:209px;background:linear-gradient(135deg,#e7a66c,#b84f7a)" role="img" aria-label="Stacked hands of a team"></div>
  <div class="abs tile" style="left:713px;top:209px;background:linear-gradient(135deg,#f0ece4,#6c9c5a)" role="img" aria-label="Cheering children in a row"></div>
</section>

<footer class="abs site-footer">
  <div class="abs agent-photo" role="img" aria-label="Portrait of branch manager Marisol Kettering"></div>
  <div class="abs agent-name">Marisol Kettering<br>Branch Manager</div>
  <div class="abs agent-info">
    Office: 469.555.0142<br>Cell: 866.555.0178<br>mkettering@brookvale.example<br>NMLS: 40219<br>2480 Larkspur Plaza, Ste. 210<br>Frisco, TX 75034
  </div>
  <div class="abs directions">Directions</div>

  <div class="abs foot-head" style="left:411px">LINKS</div>
  <ul class="abs foot-list" style="left:411px">
    <li>Home</li><li>About</li><li>Builders</li><li>Mortgage Info</li><li>Approval</li><li>Blog</li><li>Contact Us</li>
  </ul>

  <div class="abs foot-head" style="left:613px">ADDRESS</div>
  <ul class="abs foot-list" style="left:613px">
    <li>Our Address</li><li>Corporate Office - 7420 Halverson Road,</li><li>Suite 600 Dallas, Texas 75252</li><li>&nbsp;</li><li>Tel : 1-800-555-0196</li><li>Email : Contact Brookvale Funding</li>
  </ul>
  <div class="abs lang">Language...<svg width="8" height="6" viewBox="0 0 8 6"><path d="M1 1l3 3 3-3" fill="none" stroke="#ddd" stroke-width="1.2"/></svg></div>
</footer>

<div class="abs foot-bar">
  <div class="abs copy">Copyright © 2013 Brookvale Funding. All Rights Reserved</div>
  <div class="abs mini" style="left:658px;background:#5aa9d6"></div>
  <div class="abs mini" style="left:685px;background:#4a65a0"></div>
  <div class="abs mini" style="left:712px;background:#e8772a"></div>
  <div class="abs mini" style="left:744px;border:1.5px solid #ddd"></div>
</div>

</body>
</html>
```